Child Sponsorship Charity Needs a Wordpress Design

BrightWell GLOBAL is a not-for-profit organization that breaks the cycle of poverty through child sponsorship. We work in 7 countries around the world and are based in Canada. We currently have a Wordpress website and want to update the look and create a more engaging user experience. Our donor base is across Canada and our partners work across the globe. PLEASE SEE THE DESIGN BRIEF ATTACHED. We are looking for out site to be clean, colourful, and inviting. It should maintain our brand image, be welcoming to potential donors, and a great resource to current donors.

Project Deadline Extended Reason: Our Board of Directors wants a chance to provide feedback on the submissions and so we are extending the deadline to give them the opportunity to share their insights. Added Saturday, February 21, 2015

Charity

• Helvetica / Helvetica Neue

• Got a list of colours from the designer who made our logo:
• Brightwell Navy blue
• C: 100
• M: 80
• Y: 0
• K: 23
• Or
• R: 2
• G: 60
• B: 132
• Brightwell lighter blue
• C: 34
• M: 0
• Y: 3
• K: 0
• Or
• R: 161
• G: 221
• B: 241
• Brightwell deep red (newsletter accent colour)
• C: 0
• M: 91
• Y: 88
• K: 30
• Or
• R: 178
• G: 44
• B: 34

```html
<!DOCTYPE html>
<html lang="en">
<head>
<meta charset="utf-8">
<title>BrightWell GLOBAL</title>
<link href="https://fonts.googleapis.com/css2?family=Roboto:wght@400;500;700&family=Roboto+Slab:wght@700&display=swap" rel="stylesheet">
<style>
:root{
  --blue:#1f80c8;
  --blue-dark:#176aae;
  --blue-light:#3a9ae0;
  --ink:#1d1d1d;
  --text:#4a4a4a;
  --muted:#6b6b6b;
  --page:#f7f8fa;
  --footer-dark:#262626;
  --white:#ffffff;
  --line:#d7d7d7;
}
*{box-sizing:border-box;margin:0;padding:0}
html,body{width:825px;height:1200px;overflow:hidden}
body{background:var(--page);font-family:"Roboto",Helvetica,Arial,sans-serif;color:var(--text);position:relative}
.abs{position:absolute}

/* header */
.contact-phone{left:64px;top:36px;display:flex;align-items:center;gap:8px;font-size:17px;font-weight:500;color:var(--ink)}
.contact-address{left:70px;top:63px;font-size:7.5px;color:var(--ink)}
.brand{left:309px;top:4px;width:207px;height:86px;background:var(--white);display:flex;flex-direction:column;align-items:center;justify-content:center;gap:8px}
.brand-dot{width:26px;height:26px;border-radius:50%;background:var(--blue)}
.brand-name{font-size:15px;color:#3a3a3a;font-weight:400;letter-spacing:.2px}
.search{left:612px;top:39px;width:150px;height:27px;display:flex;border:1px solid #c9c9c9;border-radius:3px;background:var(--white);overflow:hidden}
.search span{flex:1;font-size:9.5px;color:#777;padding:8px 9px}
.search-btn{width:25px;background:var(--blue);display:flex;align-items:center;justify-content:center}

/* hero */
.hero{left:0;top:126px;width:825px;height:354px;background:linear-gradient(100deg,#c9b9a3 0%,#b7a58c 30%,#8c6e55 48%,#6e5a4b 62%,#b5a693 80%,#a89580 100%)}
.hero-title{left:94px;top:256px;font-family:"Roboto Slab",Georgia,serif;font-weight:700;font-size:25px;line-height:37px;color:#f4f4f4;text-shadow:0 1px 3px rgba(0,0,0,.5)}
.hero-arrow{top:268px}

/* nav */
.nav{left:64px;top:103px;width:699px;height:43px;background:linear-gradient(var(--blue-light),var(--blue-dark));display:flex;align-items:center;box-shadow:0 2px 4px rgba(0,0,0,.2)}
.nav a{color:var(--white);text-decoration:none;font-size:10px;height:43px;display:flex;align-items:center}
.nav a.active{background:#0a0a0a;width:64px;justify-content:center}

/* welcome */
.welcome-title{left:62px;top:522px;font-size:14.5px;font-weight:500;color:var(--ink)}
.welcome-title span,.blog-title span,.donate-title span{color:var(--blue)}
.welcome-text{left:60px;top:547px;width:361px;font-size:9.6px;line-height:16.8px;text-align:justify}
.btn{background:linear-gradient(var(--blue-light),var(--blue-dark));color:var(--white);border-radius:3px;font-size:10px;display:flex;align-items:center;justify-content:center;box-shadow:0 1px 2px rgba(0,0,0,.25)}
.video-frame{left:438px;top:504px;width:325px;height:198px;background:var(--white);border:1px solid var(--line);box-shadow:0 1px 3px rgba(0,0,0,.15)}
.video{left:8px;top:6px;width:307px;height:183px;border-radius:4px;overflow:hidden;background:linear-gradient(110deg,#5a4436,#a08f82 40%,#d8d3cd 55%,#7b6453 80%,#4d3a2f)}
.video-play{left:138px;top:57px}
.video-bar{left:0;bottom:0;width:307px;height:26px;background:#111}

/* blog */
.blog-title{left:62px;top:741px;font-size:13px;font-weight:500;color:var(--ink)}
.blog-rule{left:150px;top:748px;width:322px;height:1px;background:#555}
.blog-arrows{left:477px;top:741px;display:flex;gap:1px}
.blog-arrows div{width:15px;height:15px;background:#111;border-radius:2px;display:flex;align-items:center;justify-content:center}
.card-img{top:770px;height:94px;border:3px solid var(--white);box-shadow:0 1px 3px rgba(0,0,0,.3)}
.card-title{top:875px;font-size:7.5px;color:var(--blue);text-transform:uppercase}
.card-text{top:890px;font-size:7px;line-height:11px;color:var(--muted);width:138px}
.card-btn{top:918px;width:61px;height:20px;font-size:7.5px}
.donate-img{left:530px;top:741px;width:232px;height:125px;border:3px solid var(--white);box-shadow:0 1px 3px rgba(0,0,0,.3);background:linear-gradient(100deg,#a89a8a,#2a3144 40%,#c9c1b7 60%,#8b7f74)}
.donate-title{left:534px;top:877px;font-size:14.5px;font-weight:400;color:var(--ink)}
.donate-text{left:535px;top:901px;width:227px;font-size:7px;color:var(--muted);white-space:nowrap;overflow:hidden}
.donate-btn{left:534px;top:918px;width:61px;height:22px;font-size:10px}

/* footer */
.footer{left:0;top:970px;width:825px;height:154px;background:var(--blue)}
.footer h3{position:absolute;top:27px;font-size:10.5px;font-weight:500;color:var(--white)}
.footer p{position:absolute;font-size:8px;color:#e7f1fa;line-height:15px}
.footer-rule{top:22px;width:1px;height:104px;background:rgba(255,255,255,.3)}
.subscribe{left:559px;top:88px;width:204px;height:26px;display:flex;background:var(--white)}
.subscribe span{flex:1;font-size:7px;color:#777;padding:9px 8px}
.subscribe b{width:45px;background:#111;color:var(--white);font-size:8px;font-weight:700;display:flex;align-items:center;justify-content:center}
.base{left:0;top:1124px;width:825px;height:76px;background:var(--footer-dark);color:#e0e0e0;font-size:8px}
.social{left:631px;top:28px;display:flex;gap:1px}
.social div{width:22px;height:22px}
</style>
</head>
<body>

<header>
  <div class="abs contact-phone">
    <svg width="17" height="17" viewBox="0 0 20 20"><circle cx="10" cy="10" r="9" fill="none" stroke="#1f80c8" stroke-width="1.8"/><path d="M7 5.5l1.6 2.4-1 1.2c.6 1.3 1.5 2.2 2.8 2.8l1.2-1 2.4 1.6-.9 1.8c-3.6-.3-6.6-3.3-6.9-6.9z" fill="#1f80c8"/></svg>
    800-555-0142
  </div>
  <div class="abs contact-address">418 Harbour Point Rd. Suite 210</div>
  <div class="abs brand">
    <div class="brand-dot"></div>
    <div class="brand-name">BrightWell GLOBAL</div>
  </div>
  <div class="abs search">
    <span>Search</span>
    <div class="search-btn"><svg width="13" height="13" viewBox="0 0 14 14"><circle cx="5.5" cy="5.5" r="4" fill="none" stroke="#fff" stroke-width="1.6"/><path d="M8.5 8.5l4 4" stroke="#fff" stroke-width="1.8"/></svg></div>
  </div>
</header>

<section class="abs hero" role="img" aria-label="Photo of two smiling boys hugging on a dusty village road"></section>
<h1 class="abs hero-title">BRIGHTWELL<br>GLOBAL</h1>
<svg class="abs hero-arrow" style="left:26px" width="20" height="46" viewBox="0 0 20 46"><path d="M18 1L2 23l16 22" fill="none" stroke="#fff" stroke-width="1.5"/></svg>
<svg class="abs hero-arrow" style="left:780px" width="20" height="46" viewBox="0 0 20 46"><path d="M2 1l16 22L2 45" fill="none" stroke="#fff" stroke-width="1.5"/></svg>

<nav class="abs nav">
  <a class="active" href="#">HOME</a>
  <a href="#" style="margin-left:20px">ABOUT US</a>
  <a href="#" style="margin-left:38px">PROGRAMS</a>
  <a href="#" style="margin-left:38px">WHERE WE WORK</a>
  <a href="#" style="margin-left:38px">GET INVOLED</a>
  <a href="#" style="margin-left:38px">CONTACT</a>
  <a href="#" style="margin-left:38px">BLOG</a>
  <a href="#" style="margin-left:38px">DONATE</a>
</nav>

<section>
  <h2 class="abs welcome-title">WELCOME TO <span>BRIGHTWELL GLOBAL</span></h2>
  <p class="abs welcome-text">&nbsp;Lorem Ipsum has been the industry's standard dummy text ever since the 1500s, when an unknown printer took a galley of type and scrambled it to make a type specimen book. It has survived not only five centuries, but also the leap into electronic typesetting, remaining essentially unchanged. It was popularised in the 1960s with the release of Lettrex sheets containing Lorem Ipsum passages, and more recently with desktop publishing</p>
  <div class="abs btn" style="left:61px;top:668px;width:84px;height:25px">READ MORE</div>

  <div class="abs video-frame">
    <div class="abs video" role="img" aria-label="Video still of two young girls in white dresses">
      <svg class="abs video-play" width="34" height="34" viewBox="0 0 34 34"><circle cx="17" cy="17" r="17" fill="rgba(0,0,0,.55)"/><path d="M13 10l11 7-11 7z" fill="#fff"/></svg>
      <svg class="abs video-bar" width="307" height="26" viewBox="0 0 307 26">
        <rect width="307" height="26" fill="#111"/>
        <circle cx="16" cy="13" r="5.5" fill="none" stroke="#fff" stroke-width="1.3"/><path d="M14.5 10.5l4 2.5-4 2.5z" fill="#fff"/>
        <path d="M32 11h2l3-2v8l-3-2h-2z" fill="#d0283a"/>
        <g fill="#d0283a"><rect x="46" y="10" width="1.2" height="6"/><rect x="49" y="10" width="1.2" height="6"/><rect x="52" y="10" width="1.2" height="6"/><rect x="55" y="10" width="1.2" height="6"/></g>
        <g fill="#888"><rect x="58" y="10" width="1.2" height="6"/><rect x="61" y="10" width="1.2" height="6"/></g>
        <rect x="78" y="12" width="135" height="2" fill="#555"/><rect x="78" y="12" width="47" height="2" fill="#d0283a"/>
        <text x="221" y="16" font-size="7" fill="#ccc" font-family="Roboto,sans-serif">01:30 / 04:55</text>
        <rect x="271" y="10" width="8" height="6" fill="none" stroke="#fff"/>
        <circle cx="292" cy="13" r="3" fill="none" stroke="#fff" stroke-width="2" stroke-dasharray="2 1.2"/>
      </svg>
    </div>
  </div>
</section>

<section>
  <h2 class="abs blog-title">LATEST <span>BLOG</span></h2>
  <div class="abs blog-rule"></div>
  <div class="abs blog-arrows">
    <div><svg width="7" height="9" viewBox="0 0 7 9"><path d="M6 1L2 4.5 6 8" fill="none" stroke="#fff" stroke-width="1.3"/></svg></div>
    <div><svg width="7" height="9" viewBox="0 0 7 9"><path d="M1 1l4 3.5L1 8" fill="none" stroke="#fff" stroke-width="1.3"/></svg></div>
  </div>

  <div class="abs card-img" style="left:63px;width:143px;background:linear-gradient(110deg,#6a4a36,#a68466 45%,#4e5f6c)" role="img" aria-label="Photo of a smiling girl with a classmate"></div>
  <div class="abs card-title" style="left:65px">Ipsum is simply dummy text</div>
  <div class="abs card-text" style="left:64px">Lorem Ipsum has been the industry's standard dummy text ever since</div>
  <div class="abs btn card-btn" style="left:64px">READ MORE</div>

  <div class="abs card-img" style="left:218px;width:141px;background:linear-gradient(110deg,#2b3c78,#3b2a24 45%,#5a6fa8)" role="img" aria-label="Photo of a boy writing at a school desk"></div>
  <div class="abs card-title" style="left:221px">Ipsum is simply dummy text</div>
  <div class="abs card-text" style="left:220px">Lorem Ipsum has been the industry's standard dummy text ever since</div>
  <div class="abs btn card-btn" style="left:220px">READ MORE</div>

  <div class="abs card-img" style="left:370px;width:143px;background:linear-gradient(110deg,#8a4a22,#6b3f2a 45%,#d8c9b4)" role="img" aria-label="Photo of a smiling boy in a classroom"></div>
  <div class="abs card-title" style="left:373px">Ipsum is simply dummy text</div>
  <div class="abs card-text" style="left:372px">Lorem Ipsum has been the industry's standard dummy text ever since</div>
  <div class="abs btn card-btn" style="left:372px">READ MORE</div>

  <div class="abs donate-img" role="img" aria-label="Photo of two boys standing in a village"></div>
  <h2 class="abs donate-title">Donate <span>Brightwell Global</span></h2>
  <p class="abs donate-text">Lorem Ipsum has been the industry's standard dummy text ever</p>
  <div class="abs btn donate-btn">DONATE</div>
</section>

<footer class="abs footer">
  <h3 style="left:65px">LATEST NEWS</h3>
  <p style="left:65px;top:47px;width:180px;text-align:justify">27/JULY/2015<br>Donec consectetur diam ac nibh auctor ultricies. Integer mauris lacus, consequat in luctus id, semper sed felis. Cum sociis natoque penatibus</p>
  <p style="left:192px;top:110px;font-size:6.5px">READ MORE &nbsp;&raquo;</p>
  <div class="abs footer-rule" style="left:286px"></div>

  <h3 style="left:324px">GET IN TOUCH</h3>
  <p style="left:324px;top:49px;line-height:16px">418 Harbour Point Rd. Suite 210<br>Halden, ON K7M 2B4<br>Phone 613-555-0187<br>Email: hello@brightwellglobal.org</p>
  <div class="abs footer-rule" style="left:502px"></div>

  <h3 style="left:554px">SUBSCRIBE TO NEWS</h3>
  <p style="left:556px;top:48px;line-height:14px">enter your email to receive Brightwell news<br>&amp; updates!</p>
  <div class="abs subscribe"><span>Enter Your Email Address</span><b>SUBMIT</b></div>
</footer>

<div class="abs base">
  <div class="abs" style="left:61px;top:24px">Privacy Policy &nbsp;| &nbsp;Terms Conditions &nbsp;| &nbsp;Sitemap &nbsp;| &nbsp;Contact Us</div>
  <div class="abs" style="left:60px;top:43px">Copyright © 2015 &nbsp;All Rights Reserved</div>
  <div class="abs social">
    <div style="background:#f39a1e"></div>
    <div style="background:#3fa3dc"></div>
    <div style="background:#2f4f8f"></div>
    <div style="background:#2d6fb8"></div>
    <div style="background:#3fa0c9"></div>
    <div style="background:#d8212c"></div>
  </div>
</div>

</body>
</html>
```